Laser Tattoo Removal Business Cards

We are looking for a professional business card design for a laser tattoo removal business. Ideally looking for a black business card design. The name of the business is Brightline Tattoo Removal. We place our cards at local tattoo shops so we ideally are looking for something trendy/edgy to draw both male and female clientele in.

Target Market(s)

Male/Female ages 18-60

Contact Information for Business Card

black background ideally.. hoping to stay within greys, whites and black

Font styles to use
Serif
Sans Serif

Colors
121212
a9a9a9
5c5c5c
f5f5f5
ffffff
7f7f7f
606060
848484
9d9d9d

Requirements
Must have
• Employee Info:
• Melissa Thornbury
• Chief Executive Offer
• m: 919.537.2846
• w: 919.362.4178
• f: 919.685.3907
• mthornbury@brightlinetattooremoval.example
• Address:
• 4615 Oakmere Pkwy, Suite 210
• Raleigh, NC 27654
• Website:
• www.brightlinetattooremoval.example
Nice to have
• Myabe business name on back or logo on back and employee info on the front

```html
<!DOCTYPE html>
<html lang="en">
<head>
<meta charset="utf-8">
<title>Brightline Tattoo Removal – Business Card</title>
<link rel="stylesheet" href="https://fonts.googleapis.com/css2?family=Roboto:wght@400&family=Roboto+Condensed:wght@400;500&display=swap">
<style>
  :root {
    --ink: #121212;
    --white: #ffffff;
    --paper: #f5f5f5;
    --stage: #d9d9d9;
    --grey-light: #a9a9a9;
    --grey-mid: #7f7f7f;
    --grey-dark: #5c5c5c;
    --text: #3a3a3a;
  }
  * { margin: 0; padding: 0; box-sizing: border-box; }
  html, body { width: 1200px; height: 960px; overflow: hidden; }
  body {
    background: var(--stage);
    position: relative;
    font-family: "Roboto", Arial, sans-serif;
    color: var(--text);
  }
  .card {
    position: absolute;
    left: 313px;
    width: 600px;
  }
  .card--front {
    top: 113px;
    height: 343px;
    background: var(--paper);
  }
  .card--back {
    top: 472px;
    height: 343px;
    background: var(--ink);
  }
  .front-band {
    position: absolute;
    left: 0; bottom: 0;
    width: 100%; height: 5px;
    display: flex;
  }
  .front-band__dark { width: 392px; background: var(--ink); }
  .front-band__light { flex: 1; background: var(--grey-mid); }

  .brand {
    position: absolute;
    text-align: center;
    font-family: "Roboto Condensed", Arial, sans-serif;
    font-weight: 500;
    text-transform: uppercase;
  }
  .brand__name { display: block; font-size: 40px; letter-spacing: 3px; line-height: 1; }
  .brand__sub { display: block; font-size: 17px; letter-spacing: 3px; margin-top: 18px; }
  .card--front .brand { left: 30px; width: 255px; top: 128px; color: var(--ink); }
  .card--back .brand { left: 0; width: 600px; top: 108px; color: var(--grey-light); }
  .card--back .brand__name { font-size: 48px; letter-spacing: 4px; }
  .card--back .brand__sub { font-size: 20px; margin-top: 22px; }

  .divider {
    position: absolute;
    left: 280px; top: 84px;
    width: 1px; height: 188px;
    background: var(--grey-light);
  }
  .contact { position: absolute; left: 305px; top: 80px; }
  .contact__name {
    font-family: "Roboto Condensed", Arial, sans-serif;
    font-weight: 500;
    font-size: 21px;
    color: var(--ink);
    line-height: 24px;
  }
  .contact__title {
    font-family: "Roboto Condensed", Arial, sans-serif;
    font-size: 16px;
    color: var(--grey-mid);
    line-height: 18px;
  }
  .contact__address { font-size: 14px; line-height: 18px; margin-top: 7px; padding-left: 2px; }
  .contact__list { list-style: none; margin-top: 9px; }
  .contact__item {
    display: flex; align-items: center;
    font-size: 14px; line-height: 19px; height: 19px;
  }
  .contact__item--long { font-size: 12.6px; }
  .contact__icon { width: 14px; height: 14px; margin-right: 9px; fill: var(--ink); flex: none; }

  .back-web {
    position: absolute;
    left: 0; width: 600px; top: 292px;
    text-align: center;
    font-size: 13px;
    letter-spacing: 2.4px;
    color: var(--white);
  }
</style>
</head>
<body>

<section class="card card--front">
  <div class="brand">
    <span class="brand__name">Brightline</span>
    <span class="brand__sub">Tattoo Removal</span>
  </div>
  <div class="divider"></div>
  <div class="contact">
    <div class="contact__name">MELISSA THORNBURY</div>
    <div class="contact__title">Chief Executive Offer</div>
    <div class="contact__address">4615 Oakmere Pkwy, Suite 210<br>Raleigh, NC 27654</div>
    <ul class="contact__list">
      <li class="contact__item">
        <svg class="contact__icon" viewBox="0 0 24 24"><path d="M6.6 10.8a15.1 15.1 0 0 0 6.6 6.6l2.2-2.2c.3-.3.7-.4 1-.2 1.1.4 2.3.6 3.6.6.6 0 1 .4 1 1V20c0 .6-.4 1-1 1A17 17 0 0 1 3 4c0-.6.4-1 1-1h3.5c.6 0 1 .4 1 1 0 1.3.2 2.5.6 3.6.1.3 0 .7-.2 1z"/></svg>
        919.362.4178
      </li>
      <li class="contact__item">
        <svg class="contact__icon" viewBox="0 0 24 24"><path d="M7 1h10a2 2 0 0 1 2 2v18a2 2 0 0 1-2 2H7a2 2 0 0 1-2-2V3a2 2 0 0 1 2-2zm0 3v15h10V4z"/></svg>
        919.537.2846
      </li>
      <li class="contact__item">
        <svg class="contact__icon" viewBox="0 0 24 24"><path d="M6 2h10l2 2v5H6zM3 10h18a2 2 0 0 1 2 2v9H1v-9a2 2 0 0 1 2-2zm3 5v3h12v-3z"/></svg>
        919.685.3907
      </li>
      <li class="contact__item contact__item--long">
        <svg class="contact__icon" viewBox="0 0 24 24"><path d="M2 5h20v14H2zm2 2v.5l8 5 8-5V7l-8 5z"/></svg>
        mthornbury@brightlinetattooremoval.example
      </li>
      <li class="contact__item contact__item--long">
        <svg class="contact__icon" viewBox="0 0 24 24"><path d="M12 2a10 10 0 1 0 0 20 10 10 0 0 0 0-20zm-1 17.9A8 8 0 0 1 4.2 10L9 15v1a2 2 0 0 0 2 2zm6.9-2.5A2 2 0 0 0 16 16h-1v-3a1 1 0 0 0-1-1H8v-2h2a1 1 0 0 0 1-1V7h2a2 2 0 0 0 2-2v-.4a8 8 0 0 1 2.9 12.8z"/></svg>
        www.brightlinetattooremoval.example
      </li>
    </ul>
  </div>
  <div class="front-band">
    <div class="front-band__dark"></div>
    <div class="front-band__light"></div>
  </div>
</section>

<section class="card card--back">
  <div class="brand">
    <span class="brand__name">Brightline</span>
    <span class="brand__sub">Tattoo Removal</span>
  </div>
  <div class="back-web">www.brightlinetattooremoval.example</div>
</section>

</body>
</html>
```